Verlindo Magician

I want the business card for my business to give to people who watch that later I will be employed to show magic here is my website http://www.verlindoillusions.example/I want the interesting design , i am very opened for formal and informal, I watch a lot of design so don't stick to the common shape and form but i hope it can also be produced the thing to write on will be the same as in picture that i will upload , i also will upload the logo for you that so can be easy to useDenis CostilleMagicianMAGICIAN VERLINDO 17 rue des Tilleuls - 25000 BESANÇON contact@verlindoillusions.example tel. 0381 946 157 tel. 0674 219 503

```html
<!DOCTYPE html>
<html lang="fr">
<head>
<meta charset="utf-8">
<title>Verlindo Magician – Business Card</title>
<link href="https://fonts.googleapis.com/css2?family=Jost:wght@300;400;600&display=swap" rel="stylesheet">
<style>
  :root {
    --page: #e9e6e1;
    --card: #ffffff;
    --ink: #1a1a1a;
    --grey: #4a4a4a;
    --red: #e8262d;
    --portrait-dark: #111111;
    --portrait-light: #5a5a5a;
  }
  * { box-sizing: border-box; margin: 0; padding: 0; }
  html, body {
    width: 1200px; height: 1040px; overflow: hidden;
    background: var(--page);
    font-family: "Jost", "Futura", sans-serif;
    color: var(--ink);
  }
  .sheet {
    position: relative; width: 1200px; height: 1040px;
    display: flex; flex-direction: column; align-items: center;
    justify-content: center; gap: 24px;
  }
  .card {
    position: relative; width: 860px; height: 490px;
    background: var(--card);
    box-shadow: 0 6px 18px rgba(0,0,0,.18);
    overflow: hidden;
  }

  /* Front */
  .front .portrait {
    position: absolute; left: 40px; bottom: 96px;
    width: 380px; height: 300px;
    border-radius: 120px 120px 0 0;
    background: linear-gradient(160deg, var(--portrait-light), var(--portrait-dark) 55%);
  }
  .front .identity {
    position: absolute; right: 70px; top: 44px; width: 400px;
    text-align: right;
  }
  .wordmark {
    font-weight: 300; font-size: 62px; letter-spacing: 3px;
    line-height: 1; color: var(--ink);
  }
  .front .person {
    margin-top: 34px; font-size: 30px; font-weight: 400; line-height: 1.1;
  }
  .front .role {
    font-size: 22px; font-weight: 300; color: var(--red); margin-top: 2px;
  }
  .front .address {
    margin-top: 20px; font-size: 19px; font-weight: 300;
    color: var(--grey); line-height: 1.35; letter-spacing: .3px;
  }
  .contact-band {
    position: absolute; left: 0; right: 0; bottom: 18px; height: 60px;
    background: var(--red); color: #fff;
    display: flex; align-items: center; justify-content: flex-end;
    padding: 0 40px; font-size: 22px; font-weight: 400; letter-spacing: .5px;
    border-bottom: 8px solid #fff;
    box-shadow: 0 8px 0 #d9d9d9;
  }
  .contact-band b { font-weight: 600; margin-right: 6px; }
  .contact-band .sep { margin: 0 10px; }

  /* Back */
  .back .emblem {
    position: absolute; left: 50%; top: 70px; transform: translateX(-50%);
    display: flex; flex-direction: column; align-items: center; gap: 18px;
  }
  .back .portrait {
    width: 250px; height: 180px;
    border-radius: 90px 90px 0 0;
    background: linear-gradient(160deg, var(--portrait-light), var(--portrait-dark) 55%);
  }
  .back .wordmark { font-size: 46px; }
  .back .website {
    position: absolute; left: 0; right: 0; bottom: 54px;
    text-align: center; font-size: 24px; font-weight: 300;
    letter-spacing: 3px; color: var(--grey);
  }
</style>
</head>
<body>
<main class="sheet">
  <section class="card front">
    <div class="portrait" role="img" aria-label="Black and white illustration of the magician holding a playing card"></div>
    <div class="identity">
      <div class="wordmark">VERLINDO</div>
      <p class="person">Marc Ravoulet</p>
      <p class="role">Magician</p>
      <p class="address">MAGICIAN VERLINDO<br>17 rue des Tilleuls - 25000 BESANÇON</p>
    </div>
    <div class="contact-band">
      <span><b>P:</b>0381 946 157</span><span class="sep">|</span><span>0674 219 503</span>
      <span class="sep"></span><span><b>E:</b>contact@verlindoillusions.example</span>
    </div>
  </section>

  <section class="card back">
    <div class="emblem">
      <div class="portrait" role="img" aria-label="Black and white illustration of the magician holding a playing card"></div>
      <div class="wordmark">VERLINDO</div>
    </div>
    <p class="website">www.verlindoillusions.example</p>
  </section>
</main>
</body>
</html>
```